Engagement party email invitation

I need an invitation designed for my upcoming engagement party. I would like the attached picture to be encircled by gum leaves or some sort of garland of green leaves.

Traditional text typeface eg Sackers Gothic Light or Mrs Eaves.

Thanks
Marnie

Font styles to use
Serif
Script

```html
<!DOCTYPE html>
<html lang="en">
<head>
<meta charset="utf-8">
<title>Engagement Party Invitation – Patrick &amp; Marnie</title>
<link rel="stylesheet" href="https://fonts.googleapis.com/css2?family=Cinzel:wght@500;600&family=Cormorant+Garamond:ital,wght@1,500&display=swap">
<style>
  :root {
    --sky: #eef5fb;
    --haze: #dde9f3;
    --water: #b9d2e6;
    --water-deep: #9fbfd8;
    --foliage: #c9d4bf;
    --roof: #d9c3bd;
    --gold-light: #f6d58a;
    --gold-mid: #d49a3c;
    --gold-dark: #8a5418;
    --shadow: rgba(70, 40, 10, 0.55);
  }
  html, body {
    margin: 0;
    padding: 0;
    width: 1200px;
    height: 617px;
    overflow: hidden;
    background: #ffffff;
  }
  .invitation {
    position: relative;
    width: 1200px;
    height: 617px;
    overflow: hidden;
    background: var(--sky);
  }
  .harbour-scene {
    position: absolute;
    inset: 0;
    background:
      radial-gradient(ellipse 45% 55% at 12% 70%, var(--foliage) 0%, rgba(201,212,191,0) 70%),
      radial-gradient(ellipse 30% 30% at 10% 95%, var(--roof) 0%, rgba(217,195,189,0) 70%),
      radial-gradient(ellipse 70% 45% at 72% 80%, var(--water) 0%, rgba(185,210,230,0) 75%),
      linear-gradient(180deg, var(--sky) 0%, var(--sky) 25%, var(--haze) 38%, var(--water-deep) 60%, var(--water) 100%);
  }
  .invitation-text {
    position: absolute;
    inset: 0;
    text-align: center;
  }
  .gold {
    background: linear-gradient(180deg, var(--gold-light) 0%, var(--gold-mid) 55%, var(--gold-dark) 100%);
    -webkit-background-clip: text;
    background-clip: text;
    color: transparent;
    filter: drop-shadow(1px 2px 1px var(--shadow));
    margin: 0;
    position: absolute;
    left: 0;
    right: 0;
    white-space: nowrap;
  }
  .hosts, .event-details {
    font-family: "Cinzel", "Times New Roman", serif;
    font-weight: 600;
    letter-spacing: 1px;
  }
  .hosts { font-size: 44px; line-height: 1.2; }
  .hosts-line-1 { top: 38px; }
  .hosts-line-2 { top: 100px; }
  .couple {
    font-family: "Cormorant Garamond", "Georgia", serif;
    font-style: italic;
    font-weight: 500;
    font-size: 124px;
    line-height: 1;
    top: 222px;
    letter-spacing: 2px;
  }
  .event-details { font-size: 44px; line-height: 1.2; }
  .event-date { top: 420px; }
  .event-venue { top: 474px; }
</style>
</head>
<body>
  <main class="invitation">
    <div class="harbour-scene" role="img" aria-label="Soft watercolour view of a harbour with bushland, houses, moored boats and a distant city skyline"></div>
    <section class="invitation-text">
      <p class="gold hosts hosts-line-1">Robert &amp; Catherine Fairley invite you</p>
      <p class="gold hosts hosts-line-2">celebrate the engagement of</p>
      <h1 class="gold couple">Patrick &amp; Marnie</h1>
      <p class="gold event-details event-date">Saturday 23 January 2021, 6.30pm</p>
      <p class="gold event-details event-venue">14 Harbour View Road, Elm Point</p>
    </section>
  </main>
</body>
</html>
```